Fun relaxed Travel Photography Business Card*

Require a fun, funky and quirky but rememberable business card for a travel photographer

Industry/Entity Type

Photographer

Contact Information for Business Card

Front Card

(my name) Lenn D.

Travel Photographer ( small under travel photographer) “self-proclaimed”

(website logo) wanderingsoflenn.net

(PhotoFeed logo) @wanderings_of_lenn

(PhotoFeed logo) @wanderings_of_lenn_2.0 (backup for when PhotoFeed puts Lenn on timeout for bad behaviour)

Tel: N/A (removing the potential awkwardness of me not replying)

Email: (see above)

Back Card

Offending people since 1986

(Bottom right corner) “p.s. travelling made me fatTER”

Font styles to use
Serif

Colors

Designer to choose colors to be used in the design.

Requirements
Must have
• a camera
• a similar cartoon version of me as the "logo" see attached files, try to make as similar as possible

```html
<!DOCTYPE html>
<html lang="en">
<head>
<meta charset="utf-8">
<title>Lenn D. — Travel Photographer Business Card</title>
<link rel="stylesheet" href="https://fonts.googleapis.com/css2?family=Kaushan+Script&family=Patrick+Hand&family=Oswald:wght@400&family=Open+Sans:wght@400&display=swap">
<style>
  :root {
    --backdrop: #dcdcdc;
    --paper: #f3f3f1;
    --sun: #e8bd24;
    --sun-deep: #c9a418;
    --ink: #111111;
    --sky: #4da3dc;
    --shirt: #5b3d8c;
  }
  * { margin: 0; padding: 0; box-sizing: border-box; }
  html, body { width: 1200px; height: 1083px; overflow: hidden; background: var(--backdrop); }
  .canvas { position: relative; width: 1200px; height: 1083px; }

  .card {
    position: absolute;
    left: 160px;
    width: 880px;
    height: 503px;
    background: var(--paper);
    overflow: hidden;
    box-shadow: 0 6px 18px rgba(0,0,0,0.18);
  }
  .card--front { top: 26px; }
  .card--back { top: 554px; background: var(--sun); }
  .card__shapes { position: absolute; inset: 0; width: 100%; height: 100%; }

  .script { font-family: "Kaushan Script", cursive; color: var(--ink); position: absolute; line-height: 1; }
  .hand { font-family: "Patrick Hand", cursive; color: var(--ink); position: absolute; line-height: 1.1; }

  /* front */
  .avatar {
    position: absolute; left: 40px; top: 42px; width: 276px; height: 276px;
    border-radius: 50%;
    border: 9px solid var(--sun);
    background: radial-gradient(circle at 50% 70%, var(--shirt) 0 30%, var(--sky) 31%);
  }
  .front__name { left: 500px; top: 78px; font-size: 96px; }
  .front__tagline { left: 440px; top: 215px; font-size: 56px; }
  .front__since { left: 510px; top: 290px; font-size: 56px; }
  .front__ps { left: 44px; top: 440px; font-size: 24px; }

  /* back */
  .back__name { left: 48px; top: 22px; font-size: 92px; }
  .back__title {
    position: absolute; left: 70px; top: 134px;
    font-family: "Oswald", sans-serif; font-size: 30px; letter-spacing: 1px; color: var(--ink);
  }
  .back__sub {
    position: absolute; left: 70px; top: 176px;
    font-family: "Open Sans", sans-serif; font-size: 26px; color: #ffffff;
  }
  .plane {
    position: absolute; left: 640px; top: 100px; width: 190px; height: 150px;
    border-radius: 40%;
    background: linear-gradient(135deg, #e9e9ef, #bfc0c8);
  }
  .contacts { position: absolute; left: 40px; top: 330px; list-style: none; }
  .contacts li { display: flex; align-items: center; gap: 10px; font-family: "Patrick Hand", cursive; font-size: 23px; color: var(--ink); height: 34px; }
  .contacts .platform { font-size: 17px; }
  .contacts__note { position: absolute; left: 40px; top: 440px; font-size: 20px; }
  .direct { position: absolute; left: 680px; top: 320px; font-family: "Patrick Hand", cursive; color: var(--ink); }
  .direct__row { display: flex; align-items: center; gap: 8px; font-size: 26px; }
  .direct__note { font-size: 18px; line-height: 1.05; margin: 2px 0 8px 26px; }
</style>
</head>
<body>
<main class="canvas">

  <section class="card card--front">
    <svg class="card__shapes" viewBox="0 0 880 503" preserveAspectRatio="none" aria-hidden="true">
      <path fill="var(--sun-deep)" d="M0,262 Q30,232 62,250 Q92,226 122,252 Q160,242 170,272 L260,300 Q300,290 330,320 Q370,312 385,340 C420,430 560,478 700,490 L880,478 L880,503 L0,503 Z"/>
      <path fill="var(--sun)" d="M0,272 Q30,242 62,260 Q92,236 122,262 Q160,252 170,282 L260,310 Q300,300 330,330 Q370,322 385,350 C420,440 560,488 700,500 L880,490 L880,503 L0,503 Z"/>
    </svg>
    <div class="avatar" role="img" aria-label="Cartoon portrait of the photographer in sunglasses and a floral shirt with a camera around his neck"></div>
    <div class="script front__name">Lenn D.</div>
    <div class="script front__tagline">Offending people</div>
    <div class="script front__since">since 1986</div>
    <div class="hand front__ps">P.S. traveling made me fat(TER)</div>
  </section>

  <section class="card card--back">
    <svg class="card__shapes" viewBox="0 0 880 503" preserveAspectRatio="none" aria-hidden="true">
      <path fill="var(--sun-deep)" d="M0,227 Q250,312 520,290 Q555,300 545,330 Q590,340 572,372 Q612,390 586,420 Q626,442 594,470 Q620,492 604,503 L0,503 Z"/>
      <path fill="var(--paper)" d="M0,237 Q250,322 515,300 Q545,310 535,338 Q578,350 560,380 Q600,398 574,428 Q612,450 582,476 Q606,494 592,503 L0,503 Z"/>
      <circle cx="585" cy="318" r="9" fill="var(--paper)"/>
      <circle cx="615" cy="360" r="16" fill="var(--paper)"/>
      <circle cx="630" cy="420" r="22" fill="var(--paper)"/>
      <circle cx="628" cy="478" r="12" fill="var(--paper)"/>
    </svg>
    <div class="script back__name">Lenn D.</div>
    <div class="back__title">TRAVEL PHOTOGRAPHER</div>
    <div class="back__sub">self-proclaimed</div>
    <div class="plane" role="img" aria-label="Illustration of a passenger airplane seen from above"></div>
    <ul class="contacts">
      <li>
        <svg width="18" height="18" viewBox="0 0 18 18" aria-hidden="true"><circle cx="9" cy="9" r="7.5" fill="none" stroke="#2f6fc4" stroke-width="1.5"/><ellipse cx="9" cy="9" rx="3.2" ry="7.5" fill="none" stroke="#2f6fc4" stroke-width="1.2"/><line x1="1.5" y1="9" x2="16.5" y2="9" stroke="#2f6fc4" stroke-width="1.2"/></svg>
        wanderingsoflenn.net
      </li>
      <li><span class="platform">PhotoFeed</span> @wanderings_of_lenn</li>
      <li><span class="platform">PhotoFeed</span> @wanderings_of_lenn_2.0</li>
    </ul>
    <div class="hand contacts__note">(backup for when PhotoFeed puts Lenn on timeout for bad behavior)</div>
    <div class="direct">
      <div class="direct__row">
        <svg width="16" height="24" viewBox="0 0 16 24" aria-hidden="true"><rect x="1.5" y="1.5" width="13" height="21" rx="2.5" fill="none" stroke="var(--ink)" stroke-width="2"/></svg>
        N/A
      </div>
      <div class="direct__note">(removing the potential<br>awkwardness of me<br>not replying)</div>
      <div class="direct__row">
        <svg width="24" height="17" viewBox="0 0 24 17" aria-hidden="true"><rect x="1" y="1" width="22" height="15" fill="var(--ink)"/><path d="M1,1 L12,10 L23,1" fill="none" stroke="var(--sun)" stroke-width="1.5"/></svg>
        (see above)
      </div>
    </div>
  </section>

</main>
</body>
</html>
```